Announcement for a New Trauma Therapy Group - Rack Card

I need a two-sided "rack" card that is 4x9 announcing a Women's Trauma and Loss Group. I am a licensed therapist and will be starting this support group for women who have experienced trauma of all kinds. In addition to groups, I offer individual, couples, and family counseling sessions.

I would like to see designs that are soft tones and use colors like muted blues, greens, and sand tones. The final design should communicate hope and healing as well as have a peaceful feel to it.

I would like a picture of a woman's profile from either the side or from behind her. (possibly a contemplative picture on a beach)

I am attaching a picture of myself to go alongside the bio information as well.

On One Side, I need the description of the group and contact info:

Mending the Weary Spirit
Women's Trauma & Loss Group
Led by Licensed Professional Counselor, Lena Marsh Pruitt

10 Week Group
Cost - $35 session
Group size limited to 10 participants

Topics Include:
What is Trauma?
How Trauma Affects Us
Creating a Feeling of Safety
Managing Trauma Triggers
Importance of Self Care
Healthy vs. Unhealthy Coping
Guilt, Shame, and Blame
Victim vs. Victimized
Grieving through Loss
Anger and Forgiveness
Imagining a Better Future

For More Information, Contact:
Lena Marsh Pruitt, LPC, LMFT
(555) 318-4926
lena@calmwatersguide.example

On Side Two:

Life hurts and does not seem fair. So what do you do when you are faced with an event in your life that knocks you off your feet? It seems no one understands what you are feeling and no one knows just what to say. It is tempting to pull away and isolate or put up a mask and pretend everything is OK.

It is my desire you know that you are not alone! There are others who understand the feelings you are going through and offer a safe place for encouraging support. I want to invite you to embark on a courageous journey of healing where you will not only learn how to "survive" after trauma and loss, but instead, learn that you can once again "thrive"!
- Lena Marsh Pruitt, LPC, LMFT

Lena Marsh Pruitt is a Licensed Professional Counselor and Licensed Marriage and Family Therapist. She is the owner of Quiet Harbor Counseling Services located in Willow Bend, KS.

Lena is a trauma survivor herself and understands firsthand the unique challenges that can arise on the journey to healing.

(Include Lena's picture next to bio)

(Attach logo and business information to this side as well.)

Target Market(s)

Women who have gone through a traumatic experience or loss and are hurting emotionally

Industry/Entity Type

Counsellor

Font styles to use
Serif
Script

Colors
fbe7d2
86cfc6
cfeae6
85abd2
cfdeed

Requirements
Must have
• Lena's picture as well as her logo and contact information must be on the card.
• One side of the card should describe the group with the following description:
• "Mending the Weary Spirit"
• Women's Trauma & Loss Group
• Led by Licensed Professional Counselor, Lena Marsh Pruitt
• 10 Week Group
• Cost - $35 session
• Group size limited to 10 participants
• Topics Include:
• What is Trauma?
• How Trauma Affects Us
• Creating a Feeling of Safety
• Managing Trauma Triggers
• Importance of Self Care
• Healthy vs. Unhealthy Coping
• Guilt, Shame, and Blame
• Victim vs. Victimized
• Grieving through Loss
• Anger and Forgiveness
• Imagining a Better Future
• For More Information, Contact:
• Lena Marsh Pruitt, LPC, LMFT
• (555) 318-4926
• lena@calmwatersguide.example
• On the second side, it must have this note from Lena:
• Life hurts and does not seem fair. So what do you do when you are faced with an event in your life that knocks you off your feet? It seems no one understands what you are feeling and no one knows just what to say. It is tempting to pull away and isolate or put up a mask and pretend everything is OK.
• It is my desire you know that you are not alone! There are others who understand the feelings you are going through and offer a safe place for encouraging support. I want to invite you to embark on a courageous journey of healing where you will not only learn how to "survive" after trauma and loss, but instead, learn that you can once again "thrive"!
• - Lena Marsh Pruitt, LPC, LMFT
• Lena Marsh Pruitt is a Licensed Professional Counselor and Licensed Marriage and Family Therapist. She is the owner of Quiet Harbor Counseling Services located in Willow Bend, KS.
• Lena is a trauma survivor herself and understands firsthand the unique challenges that can arise on the journey to healing. In addition to facilitating groups, Lena also offers individual, marriage, and family counseling.
Nice to have
• soft muted colors that are peaceful. Light blues, greens, sand colors would work well. A picture at the top of the card of either a woman or a woman's profile that is hopeful such as a woman sitting at a beach overlooking the ocean.
Should not have
• No harsh or bright bold colors. This card needs to have a peaceful feeling to it.

```html
<!DOCTYPE html>
<html lang="en">
<head>
<meta charset="utf-8">
<title>Mending the Weary Spirit – Rack Card</title>
<link href="https://fonts.googleapis.com/css2?family=Pinyon+Script&family=Roboto:ital,wght@0,300;0,400;0,500;0,700;1,700&family=Roboto+Condensed:ital,wght@0,400;0,700;1,700&family=Varela+Round&display=swap" rel="stylesheet">
<style>
  :root {
    --bg: #7a7a7a;
    --green: #9ad400;
    --green-light: #c2e86a;
    --ink: #111111;
    --body-grey: #3d3d3d;
    --brand: #5a9e1e;
    --rule: #cfe3e0;
    --dot: #9fcfc6;
    --white: #ffffff;
  }
  * { box-sizing: border-box; margin: 0; padding: 0; }
  html, body { width: 1200px; height: 1200px; overflow: hidden; background: var(--bg); }
  .canvas { position: relative; width: 1200px; height: 1200px; }
  .card {
    position: absolute; top: 60px; width: 480px; height: 1080px;
    background: var(--white); overflow: hidden;
    box-shadow: 0 6px 22px rgba(0,0,0,.35);
  }
  .card--front { left: 60px; }
  .card--back { left: 660px; }

  /* front */
  .hero-photo {
    position: absolute; left: 0; top: 0; width: 480px; height: 480px;
    background: linear-gradient(180deg, #bfa893 0%, #a89482 40%, #8d8173 75%, #7a7166 100%);
  }
  .front-shapes { position: absolute; inset: 0; }
  .title {
    position: absolute; left: 0; width: 480px; top: 448px; text-align: center;
    font-family: "Pinyon Script", cursive; font-weight: 400; color: var(--ink);
    font-size: 62px; line-height: 60px;
  }
  .subtitle {
    position: absolute; left: 0; width: 480px; top: 594px; text-align: center;
    font-family: "Varela Round", sans-serif; font-size: 15px; line-height: 20px; color: var(--ink);
  }
  .group-length {
    position: absolute; left: 0; width: 480px; top: 672px; text-align: center;
    font-family: "Roboto", sans-serif; font-size: 31px; color: var(--ink); letter-spacing: .5px;
  }
  .cost {
    position: absolute; left: 0; width: 480px; top: 713px; text-align: center;
    font-family: "Varela Round", sans-serif; font-size: 14.5px; color: var(--ink);
  }
  .topics-heading {
    position: absolute; left: 28px; top: 764px;
    font-family: "Roboto Condensed", sans-serif; font-weight: 700; font-size: 22px; color: var(--ink);
  }
  .topics { position: absolute; top: 802px; list-style: none;
    font-family: "Roboto Condensed", sans-serif; font-size: 15.5px; line-height: 20px; color: var(--ink); }
  .topics--a { left: 28px; }
  .topics--b { left: 268px; }
  .topics li { padding-left: 20px; position: relative; }
  .topics li::before { content: "✓"; position: absolute; left: 0; font-weight: 700; }
  .topics-divider { position: absolute; left: 253px; top: 800px; width: 1px; height: 118px; background: rgba(0,0,0,.3); }

  .brand {
    font-family: "Roboto", sans-serif; font-weight: 500; color: var(--brand);
    display: flex; align-items: center; gap: 10px;
  }
  .brand-dot { width: 16px; height: 16px; border-radius: 50%; background: var(--brand); flex: none; }
  .brand--front { position: absolute; left: 30px; top: 995px; font-size: 19px; line-height: 22px; }

  .contact-front {
    position: absolute; right: 27px; top: 977px; text-align: right;
    font-family: "Roboto", sans-serif; font-size: 13.5px; line-height: 23px; color: var(--ink);
  }
  .contact-front .lead { font-weight: 700; font-size: 15px; }
  .contact-front .em { font-weight: 700; font-style: italic; }

  /* back */
  .back-shapes { position: absolute; inset: 0; }
  .letter {
    position: absolute; left: 22px; width: 436px; top: 142px; text-align: center;
    font-family: "Roboto", sans-serif; font-weight: 300; font-size: 21px; line-height: 26.5px; color: var(--body-grey);
  }
  .letter p + p { margin-top: 26px; }
  .signature {
    position: absolute; right: 24px; top: 590px;
    font-family: "Roboto Condensed", sans-serif; font-weight: 700; font-style: italic; font-size: 17.5px; color: var(--ink);
  }
  .portrait {
    position: absolute; left: 23px; top: 630px; width: 152px; height: 152px; border-radius: 50%;
    border: 6px solid var(--white);
    background: radial-gradient(circle at 50% 40%, #9a8d80 0%, #857a6e 55%, #6f665c 100%);
  }
  .bio-side {
    position: absolute; left: 190px; top: 650px; width: 272px;
    font-family: "Roboto Condensed", sans-serif; font-size: 16px; line-height: 23.5px; color: var(--ink);
  }
  .bio-wide {
    position: absolute; left: 30px; top: 796px; width: 430px;
    font-family: "Roboto Condensed", sans-serif; font-size: 16px; line-height: 23.5px; color: var(--ink);
  }
  .brand--back { position: absolute; left: 30px; top: 960px; font-size: 17px; line-height: 21px; }
  .back-divider { position: absolute; left: 210px; top: 895px; width: 1px; height: 170px; background: var(--rule); }
  .contact-back { position: absolute; left: 233px; top: 922px; font-family: "Roboto", sans-serif; }
  .contact-back .name { font-size: 20px; color: #333; letter-spacing: .5px; }
  .contact-back .creds { list-style: none; margin-top: 4px; font-size: 10px; line-height: 15px; color: var(--brand); }
  .contact-back .lines { list-style: none; margin-top: 30px; font-size: 12.5px; line-height: 16px; color: #333; letter-spacing: .4px; }
  .contact-back li::before { content: "• "; color: var(--dot); }
</style>
</head>
<body>
<div class="canvas">

  <section class="card card--front">
    <div class="hero-photo" role="img" aria-label="Photo of the counselor sitting barefoot on a rock on the beach at sunset"></div>
    <svg class="front-shapes" width="480" height="1080" viewBox="0 0 480 1080" aria-hidden="true">
      <path d="M0 462 C50 440 100 425 160 418 C240 410 320 412 380 400 C425 392 455 380 480 372 L480 920 C430 925 380 930 320 934 C240 940 150 944 80 948 L0 952 Z" fill="var(--green)"/>
    </svg>
    <h1 class="title">Mending the<br>Weary Spirit</h1>
    <p class="subtitle">Women's Trauma &amp; Loss Group Led by<br>Licensed Professional Counselor, Lena Marsh Pruitt</p>
    <p class="group-length">10 WEEK GROUP</p>
    <p class="cost">Cost - $35 session Group size limited to 10 participants</p>
    <h2 class="topics-heading">Topics Include</h2>
    <ul class="topics topics--a">
      <li>What is Trauma?</li>
      <li>How Trauma Affects Us</li>
      <li>Creating a Feeling of Safety</li>
      <li>Managing Trauma Triggers</li>
      <li>Importance of Self Care</li>
      <li>Healthy vs. Unhealthy Coping</li>
    </ul>
    <div class="topics-divider"></div>
    <ul class="topics topics--b">
      <li>Guilt, Shame, and Blame</li>
      <li>Victim vs. Victimized</li>
      <li>Grieving through Loss</li>
      <li>Anger and Forgiveness</li>
      <li>Imagining a Better Future</li>
    </ul>
    <div class="brand brand--front"><span class="brand-dot"></span><span>Quiet Harbor<br>Counseling</span></div>
    <div class="contact-front">
      <div class="lead">For More Information, Contact</div>
      <div>Lena Marsh Pruitt, LPC, LMFT</div>
      <div class="em">(555) 318-4926</div>
      <div class="em">lena@calmwatersguide.example</div>
    </div>
  </section>

  <section class="card card--back">
    <svg class="back-shapes" width="480" height="1080" viewBox="0 0 480 1080" aria-hidden="true">
      <rect x="0" y="0" width="480" height="900" fill="var(--green-light)"/>
      <path d="M0 125 C90 160 180 150 270 122 C360 94 420 82 480 88 L480 900 L0 900 Z" fill="var(--green)"/>
      <path d="M0 875 C120 885 230 890 330 870 C400 855 450 835 480 820 L480 1080 L0 1080 Z" fill="var(--white)"/>
      <path d="M0 880 C120 888 230 895 330 877 C400 862 450 842 480 828" fill="none" stroke="var(--green)" stroke-width="4"/>
    </svg>
    <div class="letter">
      <p>Life hurts and does not seem fair. So what do you do when you are faced with an event in your life that knocks you off your feet? It seems no one understands what you are feeling and no one knows just what to say. It is tempting to pull away and isolate or put up a mask and pretend everything is OK.</p>
      <p>It is my desire you know that you are not alone! There are others who understand the feelings you are going through and offer a safe place for encouraging support. I want to invite you to embark on a courageous journey of healing where you will not only learn how to "survive" after trauma and loss, but instead, learn that you can once again "thrive"!</p>
    </div>
    <div class="signature">- Lena Marsh Pruitt, LPC, LMFT</div>
    <div class="portrait" role="img" aria-label="Round portrait photo of the counselor on the beach"></div>
    <p class="bio-side">Lena Marsh Pruitt is a Licensed Professional Counselor and Licensed Marriage and Family Therapist. She is the owner of Quiet Harbor Counseling Services located in Willow Bend, KS.</p>
    <p class="bio-wide">Lena is a trauma survivor herself and understands firsthand the unique challenges that can arise on the journey to healing.</p>
    <div class="brand brand--back"><span class="brand-dot"></span><span>Quiet Harbor<br>Counseling</span></div>
    <div class="back-divider"></div>
    <div class="contact-back">
      <div class="name">Lena Pruitt, LPC-S, LMFT</div>
      <ul class="creds">
        <li>Licensed Professional Counselor</li>
        <li>Licensed Marriage and Family Therapist</li>
      </ul>
      <ul class="lines">
        <li>555.318.4926</li>
        <li>lena@calmwatersguide.example</li>
      </ul>
    </div>
  </section>

</div>
</body>
</html>
```